2023 Wall Calendar Design - 11" x 8.5"

OVERVIEW:

The theme for this calendar is American (red-white-blue) and should have a modern feel. Please see website links and attached logos.

This calendar will feature screenshots and behind-the-scenes photos from all Lantern Hollow Shows found on our website.

We will supply screenshots for you to choose from via a Filecrate link once selected. Some sample screenshots are attached to get you started on design concepts.

SPECIFICATIONS:

28 PAGES – Cover, Back Cover, Inside Cover x 2, 24 calendar pages @ 2 pages / month

SIZE: 11” x 8.5” finished – excluding bleed

FULL COLOR – CMYK

See deliverables at bottom also.

DESIGN & THEME:

Each page will be 11" x 8.5" finished (excluding bleed margins) and have 2 pages for each month plus front and back cover and inside pages - total 28 pages. A sizing template is attached for your reference.

The pages will have a scoring hole for hanging on the wall.

The front cover will be a cover design that should make the calendar look appealing and reflect our brand and theme well.

Please see our websites listed below to get a feel for our branding.

INSIDE DESIGN INFO:

For the calendar date pages there will be a main photo on 1 page with a short photo description. On the dates page, the dates will be in squares so a person can write in them (IMPORTANT).

Relevant squares will also have special days in them including show premiere dates, US holidays, show stars birthdays, company anniversary, etc.

Some date pages may / can have mini photos on them as well. Some months have more than 1 photo that could be used if the design works for it.

We will supply special dates & holidays shortly but want to get started on the design style now while we complete assembly of the dates.

The inside cover pages (2) will have some info about our brand and maybe some photos that didn't make it into the main calendar pages.

The back cover can have a collage of all 12 main photos like they normally have with wall calendars that you buy on sites like Pagewheel.example.

SOME CALENDAR LAYOUTS WE LIKE:
Not necessarily the STYLE/DESIGN but the LAYOUT for content only:

https://www.pagewheel.example/shop/gridiron-harbor-hawks-2023-wall-calendar/558120047761

https://www.pagewheel.example/shop/oliver-quillon-exclusive-wprint-2023-wall-calendar/558100004826

https://www.pagewheel.example/shop/delia-fairmont-2023-square-wall-calendar-foil/558100007193

https://www.pagewheel.example/shop/rustic-banjos-2023-wall-calendar/558100007245

https://www.pagewheel.example/shop/moorwalker-2023-wall-calendar/558100009634

https://www.pagewheel.example/shop/hollow-echoes-exclusive-w-print-2023-wall-calendar/558100012957

NOTE: I've also attached a mock-up of our 2022 calendar so you can see it.

DESIGN COLLATERAL:

We've attached our corporate logos, fonts, and some sample images that can be used in the calendar to start the layout concepts.

We will be compiling special dates and featured text while we review design concepts to select our winner.

Logo font - Stencil - https://typeshelf.example/fonts/stencil

Company sites: LanternHollowEntertainment.example | LanternHollow.example

Deliverables:

Full CMYK color, print ready PDF file formatted to 350 dpi – max file size 75 MB

Use attached template to finalize file sizes & bleeds

Fully editable layered AI source file (DO NOT USE COREL DRAW – we cannot read these files)

Fully editable In Design source file

Fully editable layered PSD source file (smart objects preferred)

Supply all fonts used so we may edit the calendar later – fonts must be licensed for your commercial use already or contact us to acquire any needed fonts.

We have licenses for all Adobe & Quarvik Assets fonts. Google & Microsoft fonts are also options. If you need us to acquire fonts from Quarvik or Adobe for your use, please let us know.

We have the Adobe Creative Suite. Any files you supply must be compatible with this software for both reading AND editing – including text.

If you have any questions, please feel free to message us and ask them.

Thank you & good luck!

Target Market(s)

American entertainment fans of TV

Industry/Entity Type

Television

Colors
0054AA
0677BA
7BADD7
CADEEF
E8F1F8
EB3D1F
EC4F4E
F09395
F8D3D4
FCEDEE

Requirements
Must have
• calendar as specified with writable date squares - see brief

```html
<!DOCTYPE html>
<html lang="en">
<head>
<meta charset="utf-8">
<title>Lantern Hollow 2023 Calendar – July Drafts</title>
<link rel="stylesheet" href="https://fonts.googleapis.com/css2?family=Montserrat:wght@300;400;500;600;700;800&display=swap">
<style>
  :root {
    --board: #dcdcdc;
    --paper: #ffffff;
    --label: #333333;
    --ink: #3a3a3a;
    --muted: #c9c9c9;
    --navy: #16407f;
    --red: #c51f2c;
    --note: #6b6b6b;
    --rule: #9a9a9a;
    --cell-line: #d4d4d4;
    --lead: #1f4e9c;
  }
  * { box-sizing: border-box; margin: 0; padding: 0; }
  html, body { width: 1200px; height: 534px; overflow: hidden; }
  body {
    position: relative;
    background: var(--board);
    font-family: "Montserrat", sans-serif;
  }
  .draft-label {
    position: absolute;
    top: 60px;
    font-size: 18.5px;
    font-weight: 700;
    color: var(--label);
  }
  .page {
    position: absolute;
    top: 85px;
    width: 498px;
    height: 385px;
    background: var(--paper);
    box-shadow: 0 10px 22px rgba(0,0,0,0.14);
  }
  .page--grid { left: 79px; }
  .page--open { left: 623px; }

  .masthead__month {
    position: absolute;
    left: 22px;
    top: 28px;
    font-size: 33px;
    font-weight: 300;
    letter-spacing: 6px;
    color: #2a2a2a;
    line-height: 1;
  }
  .masthead__year {
    position: absolute;
    left: 125px;
    top: 27px;
    font-size: 32px;
    font-weight: 800;
    letter-spacing: -2px;
    color: var(--red);
    line-height: 1;
  }
  .masthead__lead {
    position: absolute;
    left: 307px;
    top: 35px;
    width: 170px;
    font-size: 8.7px;
    line-height: 10.6px;
    color: var(--lead);
  }
  .masthead__rule {
    position: absolute;
    left: 22px;
    top: 64px;
    width: 453px;
    height: 1px;
    background: var(--rule);
  }

  .weekdays {
    position: absolute;
    display: grid;
    grid-template-columns: repeat(7, 1fr);
    font-size: 8.5px;
    font-weight: 400;
    color: #8a8a8a;
  }
  .weekdays span { padding-left: 5px; }

  .month {
    position: absolute;
    display: grid;
    grid-template-columns: repeat(7, 1fr);
  }
  .day { position: relative; padding: 4px 0 0 4.5px; }
  .day__num {
    display: block;
    font-size: 14px;
    font-weight: 700;
    line-height: 1;
    color: var(--ink);
  }
  .day__note {
    display: block;
    margin-top: 2px;
    font-size: 5.6px;
    font-weight: 500;
    line-height: 6px;
    color: var(--note);
  }
  .day--other .day__num { color: var(--muted); font-weight: 600; }
  .day--sunday .day__num { color: var(--navy); }
  .day--special .day__num { color: var(--red); }

  /* Draft 1: boxed writing squares */
  .page--grid .weekdays { left: 22px; top: 79px; width: 374px; }
  .page--grid .month {
    left: 22px; top: 95px; width: 374px; height: 268px;
    grid-template-rows: repeat(6, 1fr);
    border-top: 1px solid var(--cell-line);
    border-left: 1px solid var(--cell-line);
  }
  .page--grid .day {
    border-right: 1px solid var(--cell-line);
    border-bottom: 1px solid var(--cell-line);
  }

  /* Draft 2: open layout */
  .page--open .weekdays { left: 19px; top: 75px; width: 376px; }
  .page--open .weekdays span { padding-left: 2px; }
  .page--open .month {
    left: 19px; top: 91px; width: 376px; height: 279px;
    grid-template-rows: repeat(6, 1fr);
  }
  .page--open .day { padding: 3px 0 0 2px; }
  .page--open .day__num { font-size: 14.5px; }

  .photo-strip { position: absolute; display: flex; flex-direction: column; }
  .page--grid .photo-strip { left: 401px; top: 81px; width: 74px; gap: 6px; }
  .page--grid .photo { height: 66px; }
  .page--open .photo-strip { left: 391px; top: 77px; width: 85px; gap: 7.5px; }
  .page--open .photo { height: 62px; }

  .photo--farm { background: linear-gradient(180deg, #4f6d3a 0%, #6f8a4a 45%, #3d6b2a 100%); }
  .photo--field { background: linear-gradient(180deg, #6c6a62 0%, #8a8f7d 40%, #6f9a45 70%, #5d8e3a 100%); }
  .photo--gym { background: linear-gradient(135deg, #2a2624 0%, #1f4a44 50%, #2c2a28 100%); }
  .photo--court { background: linear-gradient(135deg, #b8722f 0%, #d88a3c 45%, #c96b8a 70%, #3a2c28 100%); }
</style>
</head>
<body>

<h2 class="draft-label" style="left:78px">Draft 1</h2>
<h2 class="draft-label" style="left:622px">Draft 2</h2>

<!-- Draft 1 -->
<section class="page page--grid" aria-label="July 2023 calendar page with boxed squares">
  <header class="masthead">
    <h1 class="masthead__month">JULY</h1>
    <span class="masthead__year">2023</span>
    <p class="masthead__lead">Lorem ipsum dolor sit amet, consectetur adipiscing elit, sed do</p>
    <div class="masthead__rule"></div>
  </header>
  <div class="weekdays"><span>Sun</span><span>Mon</span><span>Tue</span><span>Wed</span><span>Thu</span><span>Fri</span><span>Sat</span></div>
  <div class="month">
    <div class="day day--other"><span class="day__num">25</span></div>
    <div class="day day--other"><span class="day__num">26</span></div>
    <div class="day day--other"><span class="day__num">27</span></div>
    <div class="day day--other"><span class="day__num">28</span></div>
    <div class="day day--other"><span class="day__num">29</span></div>
    <div class="day day--other"><span class="day__num">30</span></div>
    <div class="day"><span class="day__num">1</span></div>

    <div class="day day--sunday"><span class="day__num">2</span></div>
    <div class="day day--special"><span class="day__num">3</span><span class="day__note">-Dharma Day<br>-LHN<br>&nbsp;Anniversary</span></div>
    <div class="day day--special"><span class="day__num">4</span><span class="day__note">Independence<br>Day</span></div>
    <div class="day"><span class="day__num">5</span></div>
    <div class="day"><span class="day__num">6</span></div>
    <div class="day"><span class="day__num">7</span></div>
    <div class="day"><span class="day__num">8</span></div>

    <div class="day day--sunday"><span class="day__num">9</span></div>
    <div class="day day--special"><span class="day__num">10</span><span class="day__note">College<br>Bowl Day</span></div>
    <div class="day"><span class="day__num">11</span></div>
    <div class="day"><span class="day__num">12</span></div>
    <div class="day"><span class="day__num">13</span></div>
    <div class="day"><span class="day__num">14</span></div>
    <div class="day"><span class="day__num">15</span></div>

    <div class="day day--sunday"><span class="day__num">16</span></div>
    <div class="day"><span class="day__num">17</span></div>
    <div class="day"><span class="day__num">18</span></div>
    <div class="day day--special"><span class="day__num">19</span><span class="day__note">Marco Reyes<br>Jr.'s Birthday</span></div>
    <div class="day"><span class="day__num">20</span></div>
    <div class="day"><span class="day__num">21</span></div>
    <div class="day"><span class="day__num">22</span></div>

    <div class="day day--sunday"><span class="day__num">23</span><span class="day__note">Parents'<br>Day</span></div>
    <div class="day"><span class="day__num">24</span></div>
    <div class="day"><span class="day__num">25</span></div>
    <div class="day"><span class="day__num">26</span></div>
    <div class="day"><span class="day__num">27</span></div>
    <div class="day"><span class="day__num">28</span></div>
    <div class="day"><span class="day__num">29</span></div>

    <div class="day day--sunday"><span class="day__num">30</span></div>
    <div class="day"><span class="day__num">31</span></div>
    <div class="day day--other"><span class="day__num">1</span></div>
    <div class="day day--other"><span class="day__num">2</span></div>
    <div class="day day--other"><span class="day__num">3</span></div>
    <div class="day day--other"><span class="day__num">4</span></div>
    <div class="day day--other"><span class="day__num">5</span></div>
  </div>
  <div class="photo-strip">
    <div class="photo photo--farm" role="img" aria-label="Show still: man standing on a green tractor in a farm yard"></div>
    <div class="photo photo--field" role="img" aria-label="Show still: athlete sprinting across a grass field"></div>
    <div class="photo photo--gym" role="img" aria-label="Show still: young man seated in a weight room"></div>
    <div class="photo photo--court" role="img" aria-label="Show still: teen holding a basketball in a gym"></div>
  </div>
</section>

<!-- Draft 2 -->
<section class="page page--open" aria-label="July 2023 calendar page with open layout">
  <header class="masthead">
    <h1 class="masthead__month">JULY</h1>
    <span class="masthead__year">2023</span>
    <p class="masthead__lead">Lorem ipsum dolor sit amet, consectetur adipiscing elit, sed do</p>
    <div class="masthead__rule"></div>
  </header>
  <div class="weekdays"><span>Sun</span><span>Mon</span><span>Tue</span><span>Wed</span><span>Thu</span><span>Fri</span><span>Sat</span></div>
  <div class="month">
    <div class="day day--other"><span class="day__num">25</span></div>
    <div class="day day--other"><span class="day__num">26</span></div>
    <div class="day day--other"><span class="day__num">27</span></div>
    <div class="day day--other"><span class="day__num">28</span></div>
    <div class="day day--other"><span class="day__num">29</span></div>
    <div class="day day--other"><span class="day__num">30</span></div>
    <div class="day"><span class="day__num">1</span></div>

    <div class="day day--sunday"><span class="day__num">2</span></div>
    <div class="day day--special"><span class="day__num">3</span><span class="day__note">Dharma Day<br>LHN<br>Anniversary</span></div>
    <div class="day day--special"><span class="day__num">4</span><span class="day__note">Independence<br>Day</span></div>
    <div class="day"><span class="day__num">5</span></div>
    <div class="day"><span class="day__num">6</span></div>
    <div class="day"><span class="day__num">7</span></div>
    <div class="day"><span class="day__num">8</span></div>

    <div class="day day--sunday"><span class="day__num">9</span></div>
    <div class="day"><span class="day__num">10</span><span class="day__note">College<br>Bowl Day</span></div>
    <div class="day"><span class="day__num">11</span></div>
    <div class="day"><span class="day__num">12</span></div>
    <div class="day"><span class="day__num">13</span></div>
    <div class="day"><span class="day__num">14</span></div>
    <div class="day"><span class="day__num">15</span></div>

    <div class="day day--sunday"><span class="day__num">16</span></div>
    <div class="day"><span class="day__num">17</span></div>
    <div class="day"><span class="day__num">18</span></div>
    <div class="day day--special"><span class="day__num">19</span><span class="day__note">Marco Reyes<br>Jr.'s Birthday</span></div>
    <div class="day"><span class="day__num">20</span></div>
    <div class="day"><span class="day__num">21</span></div>
    <div class="day"><span class="day__num">22</span></div>

    <div class="day day--sunday"><span class="day__num">23</span><span class="day__note">Parents'<br>Day</span></div>
    <div class="day"><span class="day__num">24</span></div>
    <div class="day"><span class="day__num">25</span></div>
    <div class="day"><span class="day__num">26</span></div>
    <div class="day"><span class="day__num">27</span></div>
    <div class="day"><span class="day__num">28</span></div>
    <div class="day"><span class="day__num">29</span></div>

    <div class="day day--sunday"><span class="day__num">30</span></div>
    <div class="day"><span class="day__num">31</span></div>
    <div class="day day--other"><span class="day__num">1</span></div>
    <div class="day day--other"><span class="day__num">2</span></div>
    <div class="day day--other"><span class="day__num">3</span></div>
    <div class="day day--other"><span class="day__num">4</span></div>
    <div class="day day--other"><span class="day__num">5</span></div>
  </div>
  <div class="photo-strip">
    <div class="photo photo--farm" role="img" aria-label="Show still: man standing on a green tractor in a farm yard"></div>
    <div class="photo photo--field" role="img" aria-label="Show still: athlete sprinting across a grass field"></div>
    <div class="photo photo--gym" role="img" aria-label="Show still: young man seated in a weight room"></div>
    <div class="photo photo--court" role="img" aria-label="Show still: teen holding a basketball in a gym"></div>
  </div>
</section>

</body>
</html>
```